Keystonery Billboard - Financial Services Company (Investments, Tax Planning and Insurance)

Our new office has a billboard directly above the office building. We'd like something eye-catching with a strong Call to Action, with the main part of the billboard being under 7 words if possible. We'd like you to include a way to get ahold of us (either our website keystoneryllc.example or our phone number 302-418-2907. You may also include in small font something to indicate that we've been serving the area since 1980 (the DE area, the tri-state area, the Marlowe Hollow, etc.)

We offer financial planning, tax planning, and insurance, and we help our clients to focus on their goals and happiness by providing everything they need for lifelong wealth under one roof.

Our logos are attached, we use a triangle logo with green and gray. We use the tagline "discover lasting prosperity" but this does not need to be included.

Potential ideas we have seen from other financial companies-
- the concept that the driver spends more time looking at billboards than planning for their retirement
-something along the lines of "everything you need for your finances is in this building right here" planning, investments, taxes, insurance"
-don't spend your time worrying about retirement, let us help you plan for it
-are you working for your money, or is it working for you?
- retirement takes planning, we're here to help
- ready to retire? talk to us
- need investment advice?
- need help investing?
- crossing your fingers isn't a retirement plan. we can help.
- retiring soon? you need help.

Those are just general ideas, please feel free to be creative.

brand colors:
#00b585
#00b185
#000000
#ffffff
#6d6f75
#6d6f75
#6f7074
#021712
#052e24

```html
<!DOCTYPE html>
<html lang="en">
<head>
<meta charset="utf-8">
<title>Keystonery Billboard</title>
<link rel="stylesheet" href="https://fonts.googleapis.com/css2?family=Bebas+Neue&family=Poppins:wght@400;500;700&display=swap">
<style>
  :root {
    --brand-green: #008f56;
    --brand-green-dark: #007a49;
    --ink: #1f1f1f;
    --white: #ffffff;
    --paper: #ffffff;
    --gray: #6d6f75;
  }
  html, body {
    margin: 0;
    padding: 0;
    width: 1021px;
    height: 1200px;
    overflow: hidden;
    background: var(--paper);
  }
  .billboard {
    position: absolute;
    left: 30px;
    top: 460px;
    width: 960px;
    height: 280px;
    box-shadow: 0 6px 18px rgba(0,0,0,0.25);
    overflow: hidden;
  }
  .billboard-shapes {
    position: absolute;
    inset: 0;
    width: 960px;
    height: 280px;
  }
  .headline {
    position: absolute;
    left: 29px;
    top: 33px;
    margin: 0;
    font-family: "Bebas Neue", "Oswald", sans-serif;
    font-weight: 400;
    font-size: 100px;
    line-height: 100px;
    letter-spacing: 0;
    color: var(--white);
    white-space: nowrap;
    transform: scaleX(0.92);
    transform-origin: left top;
  }
  .services {
    position: absolute;
    left: 28px;
    top: 146px;
    display: flex;
    gap: 16px;
    margin: 0;
    padding: 0;
    list-style: none;
  }
  .service {
    display: flex;
    align-items: center;
    gap: 8px;
    font-family: "Poppins", sans-serif;
    font-weight: 500;
    font-size: 20.5px;
    color: var(--white);
    white-space: nowrap;
  }
  .service-icon {
    width: 32px;
    height: 32px;
    flex: none;
  }
  .brand {
    position: absolute;
    left: 30px;
    top: 214px;
    display: flex;
    flex-direction: column;
  }
  .brand-row {
    display: flex;
    align-items: center;
    gap: 8px;
  }
  .brand-mark {
    width: 22px;
    height: 22px;
    border-radius: 50%;
    background: var(--brand-green);
  }
  .brand-name {
    font-family: "Poppins", sans-serif;
    font-weight: 500;
    font-size: 27px;
    line-height: 30px;
    color: var(--brand-green);
  }
  .brand-tagline {
    font-family: "Poppins", sans-serif;
    font-weight: 400;
    font-size: 6.5px;
    letter-spacing: 1.9px;
    text-transform: uppercase;
    color: var(--gray);
    margin-left: 31px;
  }
  .phone {
    position: absolute;
    left: 246px;
    top: 206px;
    font-family: "Poppins", sans-serif;
    font-weight: 700;
    font-size: 50px;
    line-height: 60px;
    color: var(--ink);
    white-space: nowrap;
  }
</style>
</head>
<body>
  <section class="billboard">
    <svg class="billboard-shapes" viewBox="0 0 960 280">
      <defs>
        <linearGradient id="photo-tone" x1="0" y1="0" x2="1" y2="1">
          <stop offset="0" stop-color="#e4d6c3"/>
          <stop offset="0.45" stop-color="#c9b59c"/>
          <stop offset="0.7" stop-color="#4a6593"/>
          <stop offset="1" stop-color="#e9e3da"/>
        </linearGradient>
      </defs>
      <rect class="panel-green" width="960" height="280" fill="var(--brand-green)"/>
      <polygon class="headline-band" points="0,24 657,24 636,129 0,129" fill="var(--ink)"/>
      <polygon class="contact-band" points="0,198 620,198 607,280 0,280" fill="var(--white)"/>
      <polygon class="photo-border" points="672,0 960,0 960,280 612,280" fill="var(--white)"/>
      <polygon class="photo-side" points="953,0 960,0 960,280 898,280" fill="var(--brand-green)"/>
      <g role="img" aria-label="Photo of a smiling couple sitting together reviewing financial papers over coffee">
        <polygon points="682,0 953,0 898,280 620,280" fill="url(#photo-tone)"/>
      </g>
    </svg>

    <h1 class="headline">HOW'S YOUR 401(K)?</h1>

    <ul class="services">
      <li class="service">
        <svg class="service-icon" viewBox="0 0 32 32" aria-hidden="true">
          <circle cx="16" cy="16" r="14.5" fill="var(--ink)" stroke="var(--white)" stroke-width="1.5"/>
          <rect x="10" y="9" width="12" height="14" rx="1" fill="none" stroke="var(--white)" stroke-width="1.3"/>
          <line x1="12.5" y1="13" x2="19.5" y2="13" stroke="var(--white)" stroke-width="1.2"/>
          <line x1="12.5" y1="16" x2="19.5" y2="16" stroke="var(--white)" stroke-width="1.2"/>
          <line x1="12.5" y1="19" x2="17" y2="19" stroke="var(--white)" stroke-width="1.2"/>
        </svg>
        Financial planning
      </li>
      <li class="service">
        <svg class="service-icon" viewBox="0 0 32 32" aria-hidden="true">
          <circle cx="16" cy="16" r="14.5" fill="var(--ink)" stroke="var(--white)" stroke-width="1.5"/>
          <rect x="10.5" y="8.5" width="11" height="15" rx="1" fill="none" stroke="var(--white)" stroke-width="1.3"/>
          <rect x="12.5" y="10.5" width="7" height="3" fill="var(--white)"/>
          <rect x="12.5" y="15.5" width="2" height="2" fill="var(--white)"/>
          <rect x="15" y="15.5" width="2" height="2" fill="var(--white)"/>
          <rect x="17.5" y="15.5" width="2" height="2" fill="var(--white)"/>
          <rect x="12.5" y="19" width="2" height="2" fill="var(--white)"/>
          <rect x="15" y="19" width="2" height="2" fill="var(--white)"/>
          <rect x="17.5" y="19" width="2" height="2" fill="var(--white)"/>
        </svg>
        Tax planning
      </li>
      <li class="service">
        <svg class="service-icon" viewBox="0 0 32 32" aria-hidden="true">
          <circle cx="16" cy="16" r="14.5" fill="var(--ink)" stroke="var(--white)" stroke-width="1.5"/>
          <path d="M16 8 L22 10.5 V15.5 C22 19.5 19.2 22 16 23.5 C12.8 22 10 19.5 10 15.5 V10.5 Z" fill="none" stroke="var(--white)" stroke-width="1.3"/>
          <polyline points="13.2,15.8 15.3,18 19,13.8" fill="none" stroke="var(--white)" stroke-width="1.4"/>
        </svg>
        Insurance
      </li>
    </ul>

    <div class="brand">
      <div class="brand-row">
        <span class="brand-mark" aria-hidden="true"></span>
        <span class="brand-name">Keystonery</span>
      </div>
      <span class="brand-tagline">discover lasting prosperity</span>
    </div>

    <a class="phone">302-418-2907</a>
  </section>
</body>
</html>
```